Chartered Professional Accounting Firm Needs a Business Card Design

We need a card design for an accounting firm based in Toronto, Ontario. The firm name is Pavel Ostrom Professional Corporation. The owner of the firm is a chartered professional accountant and a certified general accountant. Services of the firm include 60% tax preparation and consulting and 40% financial statements for corporation year-end. We would like a modern design. The color could be black, white, gray, blue or other color to bring more confidence to clients. The logo of the firm should be included in the design. Thanks

Name: Pavel Ostrom, CPA, CGA Address: 47 Maple Crest Rd. Richmond Hill, ON L7K 3B5 Telephone: (416) 562-3907 Fax:(416) 734-2165 Email: pavel@pavelostrom-example.ca

Accounting

```html
<!DOCTYPE html>
<html lang="en">
<head>
<meta charset="utf-8">
<title>Pavel Ostrom Professional Corporation — Business Card</title>
<link rel="stylesheet" href="https://fonts.googleapis.com/css2?family=Cinzel:wght@400;700&family=Lato:wght@400;700&display=swap">
<style>
  :root {
    --page-bg: #e9e7e3;
    --card-white: #ffffff;
    --brand-blue: #2b3490;
    --band-light: #c4c4c4;
    --band-dark: #5f5f5f;
    --text-gray: #6d6d6d;
    --text-white: #ffffff;
  }
  * { margin: 0; padding: 0; box-sizing: border-box; }
  html, body { width: 1200px; height: 800px; overflow: hidden; background: var(--page-bg); }
  .card {
    position: absolute; left: 75px; top: 100px; width: 1050px; height: 600px;
    background: var(--card-white); box-shadow: 0 10px 30px rgba(0,0,0,.18); overflow: hidden;
  }
  .card-bands { position: absolute; inset: 0; }
  .brand-mark {
    position: absolute; left: 70px; top: 62px; width: 150px; height: 150px;
    background: var(--brand-blue);
  }
  .firm-name {
    position: absolute; left: 255px; top: 52px;
    font-family: "Cinzel", serif; font-weight: 700; color: var(--brand-blue);
  }
  .firm-name .primary { display: block; font-size: 92px; line-height: 1; letter-spacing: 1px; }
  .firm-name .secondary { display: block; font-size: 37px; line-height: 1.05; letter-spacing: 1.5px; margin-top: 2px; }
  .credentials-line {
    position: absolute; left: 258px;
    font-family: "Cinzel", serif; font-weight: 400; color: var(--text-gray);
    font-size: 28px; letter-spacing: 4px; line-height: 1;
  }
  .credentials-line.cpa { top: 188px; }
  .credentials-line.cga { top: 220px; letter-spacing: 7.2px; }
  .phone-main {
    position: absolute; left: 60px; top: 255px;
    font-family: "Lato", sans-serif; font-size: 24px; color: #555; letter-spacing: 1px;
  }
  .email {
    position: absolute; right: 40px; top: 335px;
    font-family: "Lato", sans-serif; font-size: 24px; color: var(--text-white); letter-spacing: .5px;
  }
  .owner {
    position: absolute; left: 60px; top: 322px;
    font-family: "Lato", sans-serif; color: var(--text-white);
  }
  .owner .name { display: block; font-size: 38px; font-weight: 700; letter-spacing: 1px; line-height: 1; }
  .owner .title { display: block; font-size: 19px; margin-top: 4px; letter-spacing: .5px; }
  .contact {
    position: absolute; left: 60px; top: 440px;
    font-family: "Lato", sans-serif; color: var(--text-white); font-size: 25px; letter-spacing: .5px;
  }
  .contact-row { display: flex; align-items: center; gap: 22px; }
  .contact-row svg { width: 34px; height: 30px; }
  .address { margin-top: 22px; }
</style>
</head>
<body>
  <div class="card">
    <svg class="card-bands" width="1050" height="600" viewBox="0 0 1050 600" aria-hidden="true">
      <rect x="0" y="250" width="600" height="42" fill="var(--band-light)"/>
      <rect x="600" y="326" width="450" height="44" fill="var(--band-dark)"/>
      <rect x="0" y="292" width="600" height="308" fill="var(--brand-blue)"/>
      <rect x="600" y="370" width="450" height="230" fill="var(--brand-blue)"/>
    </svg>

    <div class="brand-mark"></div>
    <h1 class="firm-name">
      <span class="primary">PAVEL OSTROM</span>
      <span class="secondary">PROFESSIONAL CORPORATION</span>
    </h1>
    <p class="credentials-line cpa">CHARTERED PROFESSIONAL ACCOUNTANT</p>
    <p class="credentials-line cga">CERTIFIED GENERAL ACCOUNTANT</p>

    <p class="phone-main">(416) 562-3907</p>
    <p class="email">pavel@pavelostrom-example.ca</p>

    <div class="owner">
      <span class="name">PAVEL OSTROM</span>
      <span class="title">CPA, CGA</span>
    </div>

    <div class="contact">
      <div class="contact-row">
        <svg viewBox="0 0 34 30" aria-label="Fax">
          <rect x="9" y="1" width="16" height="9" fill="var(--text-white)"/>
          <rect x="1" y="10" width="32" height="13" rx="2" fill="var(--text-white)"/>
          <rect x="8" y="18" width="18" height="11" fill="var(--text-white)" stroke="var(--brand-blue)" stroke-width="2"/>
        </svg>
        <span>(416) 734-2165</span>
      </div>
      <p class="address">47 Maple Crest Rd. Richmond Hill, ON L7K 3B5</p>
    </div>
  </div>
</body>
</html>
```